Business Card Design Project

We need a Business Card for an Mechanical Engineering firm in Singapore. The design should be Modern & Technical looking, yet eye catching.

Our company deals in Cutting Tools & Machine Accessories for the Manufacturing Industries such as Oil & Gas, Aero Space, etc... For more information on our Company, you can either email me or view our website www.torvalen.com.sg.

We are trying to revamp our image to give our consumers a fresh new perspective to our company, so we welcome all ideas.

Industry/Entity Type

Business

Requirements
Must have
• Must incorporate New Company Logo into the card as shown in Uploaded file.

```html
<!DOCTYPE html>
<html lang="en">
<head>
<meta charset="utf-8">
<title>Torvalen Tools – Business Card</title>
<link rel="stylesheet" href="https://fonts.googleapis.com/css2?family=Tinos:wght@400;700&display=swap">
<style>
  :root {
    --backdrop: #1f1f21;
    --card: #ffffff;
    --ink: #2b2b2b;
    --brand: #7b1d3a;
    --accent: #e8431f;
    --icon-bg: #8a8a8a;
    --gear-light: #f1f1f1;
    --gear-mid: #dcdcdc;
  }
  * { box-sizing: border-box; margin: 0; padding: 0; }
  html, body {
    width: 1200px; height: 882px; overflow: hidden;
    background: var(--backdrop);
    font-family: "Tinos", "Times New Roman", serif;
  }
  .canvas {
    width: 1200px; height: 882px;
    display: flex; align-items: center; justify-content: center;
  }
  .card {
    position: relative;
    width: 1000px; height: 600px;
    background: var(--card);
    color: var(--ink);
  }
  .card__decoration {
    position: absolute; left: 0; top: 50px;
    width: 560px; height: 400px;
    background: radial-gradient(ellipse at 30% 45%, var(--gear-mid) 0%, var(--gear-light) 45%, rgba(255,255,255,0) 75%);
  }
  .card__holder {
    position: absolute; right: 40px; top: 40px; text-align: right;
  }
  .card__holder-name { font-size: 34px; font-weight: 700; line-height: 1.1; }
  .card__holder-phone { font-size: 20px; }
  .company {
    position: absolute; left: 640px; top: 298px; width: 310px;
  }
  .company__name { font-size: 26px; font-weight: 700; letter-spacing: 0.3px; }
  .company__address { font-size: 20px; line-height: 1.35; text-align: justify; }
  .contact-list {
    position: absolute; left: 640px; top: 420px; list-style: none;
  }
  .contact-list__item {
    display: flex; align-items: center; gap: 6px; margin-bottom: 5px;
  }
  .contact-list__icon {
    width: 34px; height: 34px; background: var(--icon-bg);
    display: flex; align-items: center; justify-content: center;
  }
  .contact-list__value {
    width: 236px; height: 34px; background: var(--accent); color: #fff;
    font-size: 19px; line-height: 34px; padding-left: 10px;
  }
  .brand {
    position: absolute; left: 60px; bottom: 70px;
    display: flex; align-items: center; gap: 16px;
  }
  .brand__dot {
    width: 44px; height: 44px; border-radius: 50%; background: var(--brand);
  }
  .brand__name {
    font-size: 48px; font-weight: 700; color: var(--brand); letter-spacing: 2px;
  }
</style>
</head>
<body>
<main class="canvas">
  <article class="card">
    <div class="card__decoration" role="img" aria-label="Faint grey line illustration of interlocking machine gears"></div>

    <header class="card__holder">
      <p class="card__holder-name">Marianne</p>
      <p class="card__holder-phone">Mo 65-61234870</p>
    </header>

    <section class="company">
      <h1 class="company__name">Torvalen Tools Pte Ltd</h1>
      <p class="company__address">27 Kestrel Loop #03-08, Kestrel Industrial Hub, Singapore 609512</p>
    </section>

    <ul class="contact-list">
      <li class="contact-list__item">
        <span class="contact-list__icon">
          <svg width="20" height="20" viewBox="0 0 20 20" aria-hidden="true"><path d="M5 2h3l1 4-2 1.5a10 10 0 0 0 5.5 5.5L14 11l4 1v3a2 2 0 0 1-2 2A14 14 0 0 1 3 4a2 2 0 0 1 2-2z" fill="#fff"/></svg>
        </span>
        <span class="contact-list__value">65-61234870</span>
      </li>
      <li class="contact-list__item">
        <span class="contact-list__icon">
          <svg width="22" height="20" viewBox="0 0 22 20" aria-hidden="true"><rect x="5" y="2" width="12" height="6" fill="#fff"/><rect x="2" y="9" width="18" height="8" rx="1" fill="#fff"/></svg>
        </span>
        <span class="contact-list__value">65-61234871</span>
      </li>
      <li class="contact-list__item">
        <span class="contact-list__icon">
          <svg width="22" height="16" viewBox="0 0 22 16" aria-hidden="true"><rect x="1" y="1" width="20" height="14" fill="none" stroke="#fff" stroke-width="1.8"/><path d="M1 1l10 8 10-8" fill="none" stroke="#fff" stroke-width="1.8"/></svg>
        </span>
        <span class="contact-list__value">hello@torvalen.com.sg</span>
      </li>
    </ul>

    <div class="brand">
      <span class="brand__dot"></span>
      <span class="brand__name">TORVALEN TOOLS</span>
    </div>
  </article>
</main>
</body>
</html>
```